Flyer-Design für Kindertagesstätte
Felmriks Spielhafen suchte ein neues Design in der Kategorie Flyer und hat ein Projekt auf grafikwunsch.de gestartet.
Zielgruppe
Wir sind eine Kindertagesstätte und wollen eine Baby-Kind-Spielgruppe jeden Mittwoch in unserer Kita von 09.00 Uhr bis 11.00 Uhr anbieten.
Aufgabenstellung
Unser LOGO muss im Flyer enthalten sein, auf jeden Fall ein Bild wenn möglich mit mehreren Babys/Kleinkindern bis 1,5 Jahre. Wir benötigen den Flyer in DIN lang - bunt - 1 seitig.
Folgender Text sollte enthalten: Baby-Kind-Spielgruppe, jeden mittwoch in unserer Kita 'Felmriks Spielhafen' von 09.00 Uhr bis 11.00 Uhr. Die Spielgruppe wird durch unser ausgebildetes Fachpersonal begleitet.

```html
<!DOCTYPE html>
<html lang="de">
<head>
<meta charset="utf-8">
<title>Baby-Kind-Spielgruppe – Flyer</title>
<link href="https://fonts.googleapis.com/css2?family=Archivo+Black&family=Arimo:wght@400;700&display=swap" rel="stylesheet">
<style>
  :root {
    --stage: #cccccc;
    --orange: #d2601f;
    --orange-light: #e07a25;
    --yellow: #e6b93f;
    --yellow-light: #ecc857;
    --crimson: #c41f36;
    --dark-red: #a22228;
    --green: #7a9e22;
    --text-red: #9c1d22;
    --white: #ffffff;
    --logo-bg: #ececec;
  }
  * { margin: 0; padding: 0; box-sizing: border-box; }
  html, body { width: 1200px; height: 800px; overflow: hidden; background: var(--stage); }
  .flyer {
    position: absolute; left: 50px; top: 140px;
    width: 1100px; height: 520px; overflow: hidden;
  }
  .flyer svg.backdrop { position: absolute; inset: 0; }
  .headline {
    position: absolute; left: 420px; top: 44px;
    font-family: "Archivo Black", "Arial Black", sans-serif;
    font-size: 42px; letter-spacing: 2px; color: var(--white);
    white-space: nowrap;
  }
  .details {
    position: absolute; left: 330px; top: 120px; width: 420px;
    text-align: center; font-family: "Arimo", Arial, sans-serif; color: var(--text-red);
  }
  .details .intro { font-size: 19px; }
  .details .venue { font-size: 28px; font-weight: 700; margin-top: 18px; letter-spacing: 0.5px; }
  .details .from { font-size: 22px; margin-top: 4px; }
  .details .time { font-size: 24px; font-weight: 700; letter-spacing: 0.5px; }
  .details .note { font-size: 20px; line-height: 1.3; margin-top: 22px; }
  .brand {
    position: absolute; left: 0; top: 370px; width: 160px; height: 150px;
    background: var(--logo-bg);
    display: flex; align-items: center; justify-content: center; text-align: center;
    font-family: "Arimo", Arial, sans-serif; font-weight: 700; font-size: 17px;
    line-height: 1.2; color: var(--text-red);
  }
</style>
</head>
<body>
  <section class="flyer">
    <svg class="backdrop" width="1100" height="520" viewBox="0 0 1100 520">
      <defs>
        <linearGradient id="orange-fill" x1="0" y1="0" x2="0" y2="1">
          <stop offset="0" stop-color="var(--orange)"/>
          <stop offset="1" stop-color="var(--orange-light)"/>
        </linearGradient>
        <linearGradient id="yellow-fill" x1="0" y1="0" x2="0" y2="1">
          <stop offset="0" stop-color="var(--yellow)"/>
          <stop offset="1" stop-color="var(--yellow-light)"/>
        </linearGradient>
        <linearGradient id="child-photo" x1="0" y1="0" x2="1" y2="1">
          <stop offset="0" stop-color="#d9d6d2"/>
          <stop offset="0.6" stop-color="#b9b2ab"/>
          <stop offset="1" stop-color="#e6e0d6"/>
        </linearGradient>
        <linearGradient id="play-photo" x1="0" y1="0" x2="1" y2="1">
          <stop offset="0" stop-color="#ece8e3"/>
          <stop offset="0.5" stop-color="#cdb8a6"/>
          <stop offset="1" stop-color="#f1ece6"/>
        </linearGradient>
      </defs>
      <rect class="field-crimson" width="1100" height="520" fill="var(--crimson)"/>
      <polygon class="field-dark-red" points="0,380 285,330 520,520 0,520" fill="var(--dark-red)"/>
      <polygon class="field-orange" points="0,0 380,0 285,330 0,385" fill="url(#orange-fill)" stroke="var(--white)" stroke-width="3"/>
      <polygon class="field-green" points="660,520 780,395 1100,445 1100,520" fill="var(--green)"/>
      <polygon class="field-yellow" points="380,0 600,0 830,330 660,520 520,520 285,330" fill="url(#yellow-fill)" stroke="var(--white)" stroke-width="3"/>
      <circle class="photo-frame" cx="150" cy="148" r="150" fill="url(#child-photo)" stroke="#eeeeee" stroke-width="4"
              role="img" aria-label="Foto: Kleinkind spielt mit einem bunten Stapelturm"/>
      <circle class="photo-frame" cx="960" cy="345" r="162" fill="url(#play-photo)" stroke="#eeeeee" stroke-width="4"
              role="img" aria-label="Foto: Erzieherin klatscht mit einem Baby ab"/>
    </svg>

    <h1 class="headline">Baby-Kind-Spielgruppe</h1>

    <div class="details">
      <p class="intro">jeden Mittwoch in unserer Kita</p>
      <p class="venue">„Felmriks Spielhafen“</p>
      <p class="from">von</p>
      <p class="time">09.00 Uhr bis 11.00 Uhr</p>
      <p class="note">Die Spielgruppe wird durch unser<br>ausgebildetes Fachpersonal<br>begleitet.</p>
    </div>

    <div class="brand">Felmriks<br>Spielhafen</div>
  </section>
</body>
</html>
```